Zestora - Landing Page

Need a landing page for a journal app. The app is based on a retrospective board, where each journal entry is split into 3 sections: "What went well", "What Didn't Go Well" and "Things To Try".
The landing page should match the style of all modern web application landing pages. Think Brint, Tivalo, Mirvane. I've included screenshots of the app.
One feature that I want to highlight that is not ready yet, is an AI coach. It will offer insights based on the history of the user's journal entries
1 page

```html
<!DOCTYPE html>
<html lang="en">
<head>
<meta charset="utf-8">
<title>Zestora – Journal App</title>
<link href="https://fonts.googleapis.com/css2?family=Poppins:wght@400;500;600;700&family=Nunito+Sans:wght@400;600;700&display=swap" rel="stylesheet">
<style>
:root{
  --ink:#1b2130;
  --muted:#4a5163;
  --blue:#2f6fed;
  --blue-soft:#5d9cf6;
  --pink:#f6a999;
  --yellow:#fde29a;
  --app-dark:#1f2937;
  --line:#e3e6ec;
  --panel:#f4f5f8;
  --coach-bg:#eef4ff;
  --white:#ffffff;
  --head:'Poppins',sans-serif;
  --body:'Nunito Sans',sans-serif;
}
*{box-sizing:border-box;margin:0;padding:0}
html,body{width:1200px;height:3572px;overflow:hidden}
body{position:relative;background:var(--white);font-family:var(--body);color:var(--ink)}
.abs{position:absolute}
.btn{position:absolute;background:var(--blue);color:var(--white);font:600 15px var(--head);border-radius:6px;display:flex;align-items:center;justify-content:center}

/* header */
.brand{left:20px;top:28px;display:flex;align-items:center;gap:12px;font:600 26px var(--head)}
.brand-mark{width:30px;height:30px;border:4px solid var(--ink);border-radius:4px}
.nav{left:480px;top:48px;display:flex;gap:26px;font:500 14px var(--body);color:var(--ink)}
.nav .active{border-bottom:2px solid var(--ink)}

/* hero */
.hero-welcome{top:132px;width:100%;text-align:center;font:600 40px var(--head)}
.hero-title{top:186px;width:100%;text-align:center;font:700 52px var(--head)}
.hero-sub{top:262px;left:380px;width:440px;text-align:center;font:400 17px/1.5 var(--body)}

/* app mockups */
.app{position:absolute;background:var(--white);border:1px solid var(--line);border-radius:6px;overflow:hidden;box-shadow:0 10px 30px rgba(20,30,60,.12)}
.app-side{position:absolute;left:0;top:0;bottom:0;background:var(--app-dark)}
.app-side i{display:block;width:10px;height:10px;border-radius:2px;background:#6b7385;margin:14px auto 0}
.chip{position:absolute;font:600 10px var(--body);border:1px solid var(--line);border-radius:4px;padding:3px 8px;background:var(--white)}
.entry-date{font:700 12px var(--body);margin-bottom:8px}
.entry-line{font:400 10px/1.7 var(--body);color:var(--muted)}
.entry-block{position:absolute;left:70px;right:40px;border-bottom:1px solid var(--line);padding-bottom:14px}

.illus{position:absolute;border-radius:8px}

/* intro */
.intro{top:1000px;left:200px;width:800px;text-align:center}
.intro h2{font:600 32px/1.35 var(--head)}
.intro p{font:400 32px/1.4 var(--head);margin-top:2px}

/* feature sections */
.feature h3{font:700 32px var(--head);margin-bottom:22px}
.feature h4{font:700 17px var(--body);margin-bottom:10px}
.feature p{font:400 14px/1.6 var(--body);color:var(--muted)}
.feature .btn{position:static;width:116px;height:40px;margin-top:22px}
.block{position:absolute}
.card{position:absolute;background:var(--white);border:1px solid var(--line);border-radius:4px;box-shadow:0 6px 18px rgba(20,30,60,.15);padding:14px}
.card-title{font:700 11px var(--body);margin-bottom:10px}
.card li{list-style:none;font:400 10px/1.6 var(--body);color:var(--muted);padding-left:10px;position:relative}
.card li::before{content:"";position:absolute;left:0;top:6px;width:4px;height:4px;border-radius:50%;background:var(--muted)}
.col{position:absolute;background:var(--panel);border:1px solid var(--line);border-radius:3px}

/* coach */
.coach{top:2760px;left:0;width:1200px;height:560px;background:linear-gradient(180deg,var(--white),var(--coach-bg))}
.coach h2{position:absolute;top:160px;width:100%;text-align:center;font:700 34px/1.25 var(--head)}
.coach p{position:absolute;top:250px;left:360px;width:500px;text-align:center;font:400 14px/1.6 var(--body);color:var(--muted)}

/* footer */
.footer{top:3320px;left:0;width:1200px;height:252px;background:var(--white)}
.foot-col h5{font:700 14px var(--body);margin-bottom:12px;letter-spacing:.5px}
.foot-col a{display:block;font:400 14px/1.55 var(--body);color:var(--ink);text-decoration:none}
.contact-row{display:flex;gap:12px;font:400 14px/1.45 var(--body);margin-bottom:10px}
.contact-row svg{flex:none;margin-top:3px}
.foot-line{left:0;top:3512px;width:1200px;height:1px;background:var(--line)}
.copy{left:112px;top:3530px;font:400 14px var(--body)}
.social{left:902px;top:3524px;display:flex;gap:10px}
.social i{display:block;width:26px;height:26px;border:1.5px solid var(--ink);border-radius:50%}
</style>
</head>
<body>

<!-- header -->
<div class="abs brand"><span class="brand-mark"></span>Zestora</div>
<nav class="abs nav">
  <span class="active">Home</span><span>Features ▾</span><span>Solutions</span><span>Pricing</span><span>Resources ▾</span><span>Contact</span>
</nav>
<div class="btn" style="left:962px;top:40px;width:126px;height:40px">Get Started</div>

<!-- hero -->
<div class="abs hero-welcome">Welcome!</div>
<h1 class="abs hero-title">Reflect. Learn. Grow.</h1>
<p class="abs hero-sub">A guided journaling experience designed to help you turn reflection into action.</p>
<div class="btn" style="left:484px;top:326px;width:232px;height:44px">Start Journaling Today</div>

<div class="app" style="left:222px;top:402px;width:780px;height:576px">
  <div class="app-side" style="width:42px"><i></i><i></i><i></i><i></i><i></i></div>
  <div class="chip" style="left:70px;top:24px">+ Add Entry</div>
  <div class="chip" style="right:40px;top:24px;background:#2fbf71;color:#fff;border-color:#2fbf71">Save</div>
  <div class="entry-block" style="top:70px">
    <div class="entry-date">Tue Aug 22 2024</div>
    <div class="entry-line">Finished the weekly report early</div>
    <div class="entry-line">Had a calm morning walk</div>
    <div class="entry-line">Skipped lunch again today</div>
    <div class="entry-line">Plan meals the night before</div>
    <div class="entry-line">Try a short evening stretch</div>
  </div>
  <div class="entry-block" style="top:520px;border:none">
    <div class="entry-date">Mon Aug 21 2024</div>
    <div class="entry-line">Good talk with the team</div>
  </div>
</div>
<div class="illus" role="img" aria-label="Illustration of a person writing with a large pen" style="left:960px;top:510px;width:210px;height:330px;background:linear-gradient(160deg,#eef0f4,#d9dde5)"></div>

<!-- intro -->
<div class="abs intro">
  <h2>Our journal app is designed to help you reflect on your day in a structured way.</h2>
  <p>Each entry is divided into three sections</p>
</div>

<!-- section 1 -->
<div class="abs feature" style="left:112px;top:1252px;width:450px">
  <h3>What Went Well</h3>
  <h4>Celebrate your successes &amp; positive moments.</h4>
  <p>Lorem ipsum dolor sit amet, consectetur adipiscing elit, sed do eiusmod tempor incididunt ut labore et dolore magna aliqua. Quis ipsum suspendisse ultrices gravida. Risus commodo viverra maecenas accumsan lacus vel facilisis sed do eiusmod tempor incididunt.</p>
  <div class="btn">Learn More</div>
</div>
<div class="block" style="left:660px;top:1182px;width:540px;height:400px;background:var(--pink);border-radius:14px 0 0 14px"></div>
<div class="app" style="left:740px;top:1232px;width:460px;height:300px;box-shadow:none">
  <div class="app-side" style="width:28px"><i></i><i></i><i></i><i></i></div>
  <div class="card-title abs" style="left:44px;top:12px">Entry</div>
  <div class="chip" style="left:44px;top:32px">+ Add Item</div>
  <div class="col" style="left:44px;top:62px;width:120px;height:220px"></div>
  <div class="col" style="left:176px;top:62px;width:120px;height:220px"></div>
  <div class="col" style="left:308px;top:62px;width:120px;height:220px"></div>
</div>
<div class="card" style="left:898px;top:1296px;width:170px;height:200px">
  <div class="card-title">What Went Well</div>
  <ul><li>Completed the morning workout</li><li>Shipped the new feature</li><li>Read two book chapters</li></ul>
</div>

<div class="illus" role="img" aria-label="Illustration of a person resting on a stack of books" style="left:160px;top:1618px;width:400px;height:160px;background:linear-gradient(180deg,#f1f2f5,#dfe2e8)"></div>

<!-- section 2 -->
<div class="block" style="left:0;top:1748px;width:540px;height:400px;background:var(--yellow);border-radius:0 14px 14px 0"></div>
<div class="app" style="left:0;top:1792px;width:470px;height:310px;box-shadow:none">
  <div class="app-side" style="width:28px"><i></i><i></i><i></i><i></i></div>
  <div class="card-title abs" style="left:44px;top:12px">Entry</div>
  <div class="chip" style="left:44px;top:32px">+ Add Item</div>
  <div class="col" style="left:44px;top:62px;width:120px;height:230px"></div>
  <div class="col" style="left:176px;top:62px;width:120px;height:230px"></div>
  <div class="col" style="left:308px;top:62px;width:120px;height:230px"></div>
</div>
<div class="card" style="left:120px;top:1860px;width:180px;height:210px">
  <div class="card-title">What Didn't Go Well</div>
  <ul><li>Stayed up too late again</li><li>Missed a team deadline</li><li>Skipped the daily review</li></ul>
</div>
<div class="abs feature" style="left:602px;top:1796px;width:470px">
  <h3>What Didn't Go Well</h3>
  <h4>Acknowledge challenges and areas for improvement.</h4>
  <p>Lorem ipsum dolor sit amet, consectetur adipiscing elit, sed do eiusmod tempor incididunt ut labore et dolore magna aliqua. Quis ipsum suspendisse ultrices gravida. Risus commodo viverra maecenas accumsan lacus vel facilisis sed do eiusmod tempor incididunt.</p>
  <div class="btn">Learn More</div>
</div>

<!-- section 3 -->
<div class="abs feature" style="left:112px;top:2376px;width:450px">
  <h3>Things to Try</h3>
  <h4>Plan actionable steps to make tomorrow even better.</h4>
  <p>Lorem ipsum dolor sit amet, consectetur adipiscing elit, sed do eiusmod tempor incididunt ut labore et dolore magna aliqua. Quis ipsum suspendisse ultrices gravida. Risus commodo viverra maecenas accumsan lacus vel facilisis sed do eiusmod tempor incididunt.</p>
  <div class="btn">Learn More</div>
</div>
<div class="block" style="left:660px;top:2322px;width:540px;height:440px;background:var(--blue-soft);border-radius:14px 0 0 14px"></div>
<div class="app" style="left:740px;top:2380px;width:460px;height:320px;box-shadow:none">
  <div class="app-side" style="width:28px"><i></i><i></i><i></i><i></i></div>
  <div class="card-title abs" style="left:44px;top:12px">Entry</div>
  <div class="chip" style="left:44px;top:32px">+ Add Item</div>
  <div class="col" style="left:44px;top:62px;width:120px;height:240px"></div>
  <div class="col" style="left:176px;top:62px;width:120px;height:240px"></div>
  <div class="col" style="left:308px;top:62px;width:120px;height:240px"></div>
</div>
<div class="card" style="left:900px;top:2450px;width:180px;height:220px">
  <div class="card-title">Things to Try</div>
  <ul><li>Set a fixed bedtime alarm</li><li>Block focus time each morning</li><li>Review goals every Friday</li></ul>
</div>

<!-- AI coach -->
<section class="abs coach">
  <h2>Your Personal<br>AI Coach</h2>
  <p>Get ready to take your journaling experience to the next level with our upcoming AI Coach feature. Drawing insights from your past entries, the AI Coach will offer personalized guidance, helping you identify patterns and make meaningful progress in your life.</p>
  <div class="btn" style="left:484px;top:360px;width:232px;height:44px">Start Journaling Today</div>
</section>
<div class="illus" role="img" aria-label="Illustration of a person sitting with a laptop" style="left:0;top:3080px;width:280px;height:240px;background:linear-gradient(170deg,#e6ebf5,#c9d0de)"></div>

<!-- footer -->
<footer class="abs footer">
  <div class="abs brand" style="left:112px;top:40px">
    <span class="brand-mark"></span>Zestora
  </div>
  <div class="abs foot-col" style="left:420px;top:30px">
    <h5>QUICK LINKS</h5><a>Home</a><a>Pricing</a><a>Features</a><a>Solutions</a>
  </div>
  <div class="abs foot-col" style="left:640px;top:30px">
    <h5>OTHER LINKS</h5><a>Resources</a><a>Contact Us</a><a>Terms &amp; Conditions</a><a>Privacy Policy</a>
  </div>
  <div class="abs foot-col" style="left:902px;top:30px">
    <h5>CONTACT US</h5>
    <div class="contact-row">
      <svg width="14" height="16" viewBox="0 0 14 16"><path d="M7 1a5 5 0 0 0-5 5c0 4 5 9 5 9s5-5 5-9a5 5 0 0 0-5-5z" fill="var(--ink)"/><circle cx="7" cy="6" r="2" fill="#fff"/></svg>
      <span>Zestora,<br>Address Comes Here</span>
    </div>
    <div class="contact-row">
      <svg width="14" height="14" viewBox="0 0 14 14"><path d="M3 1l2 3-1.5 1.5a8 8 0 0 0 5 5L10 9l3 2-1 2.5C6 13.5.5 8 .5 2z" fill="var(--ink)"/></svg>
      <span>+1 555 014 2290</span>
    </div>
    <div class="contact-row">
      <svg width="14" height="12" viewBox="0 0 14 12"><rect x="0.5" y="0.5" width="13" height="11" rx="1" fill="var(--ink)"/><path d="M1 1l6 5 6-5" stroke="#fff" fill="none"/></svg>
      <span>hello@zestora.app</span>
    </div>
  </div>
</footer>
<div class="abs foot-line"></div>
<div class="abs copy">2024 Zestora. All Rights Reserved.</div>
<div class="abs social"><i></i><i></i><i></i><i></i><i></i></div>

</body>
</html>
```